MirelaStyle e-commerce website design for shopify platform

I currently have a trendy e-commerce clothing store that is primarily based off of the Southern California Style/Trends. I am looking for a redesign of my shopify template as I don't like my current image. I am looking for a sleek clean design that allows more focus on the products. I like neutral backgrounds and easy to use websites. Should be responsive to mobile devices. I would also like to have some ideas for a slide show picture that notifies customers of free shipping if possible. I do also have a theme template that I purchased through Shopify so one could set the theme up for me and edit it to what I need. My website is mirelastyle.com if you would like to look at the type of products I have. I am also looking to do a logo redesign as well- looking for a more stylish logo that would appeal to an approximate age range of 18-40 year old women. I want to be remembered, something to match the web design.

I like teal/turquoise and grey combos but I don't have to have this as the colors.

Target Market(s)

approx. 18-40

Industry/Entity Type

E-Commerce

Number of Pages Required

2 page

Requirements
Must have
• Menu bar, shopify compatible, easy to access/navigate, responsive to mobile devices, easy product upload
Nice to have
• if able ability to resize pictures all to the same size
Should not have
• not be difficult to navigate both on a reg. computer or mobile device

```html
<!DOCTYPE html>
<html lang="en">
<head>
<meta charset="utf-8">
<title>MirelaStyle</title>
<link href="https://fonts.googleapis.com/css2?family=Open+Sans:wght@400;600&family=Roboto:wght@400;500&family=Playfair+Display:wght@700&display=swap" rel="stylesheet">
<style>
:root{
  --teal:#1b8f9e;
  --teal-soft:rgba(27,143,158,.8);
  --dark:#333537;
  --page:#ececec;
  --card:#ffffff;
  --line:#dcdcdc;
  --text:#555;
  --muted:#888;
  --pink:#ee3f6e;
  --red:#e8474b;
  --blue:#4aa8de;
  --magenta:#e04fc9;
}
*{box-sizing:border-box;margin:0;padding:0}
html,body{width:708px;height:1200px;overflow:hidden}
body{background:var(--page);font-family:"Open Sans",sans-serif;color:var(--text);position:relative}
.abs{position:absolute}
.topbar{left:0;top:0;width:708px;height:26px;background:var(--dark);color:#ddd;font-size:7px}
.topbar .flag{left:107px;top:8px;width:20px;height:11px;background:linear-gradient(#c8102e 0 0) center/100% 3px no-repeat,linear-gradient(#c8102e 0 0) center/3px 100% no-repeat,#1f3e86}
.topbar .cur{left:143px;top:9px}
.toplinks{right:124px;top:9px;display:flex;gap:9px}
.toplinks span+span:before{content:"|";margin-right:9px;color:#888}
.brand{left:106px;top:44px;font-family:"Roboto",sans-serif;font-weight:500;font-size:24px;color:#222;display:flex;align-items:center;gap:6px}
.brand i{width:10px;height:10px;border-radius:50%;background:var(--pink);display:block}
.search{left:388px;top:46px;width:122px;height:24px;background:#fff;border:1px solid var(--line);font-size:7px;color:#aaa;padding:8px 9px}
.search svg{position:absolute;right:7px;top:7px}
.cart{left:519px;top:46px;width:82px;height:24px;background:#fff;border:1px solid var(--line);font-size:7px;color:#777;padding:8px 0 0 27px;white-space:nowrap}
.cart svg{position:absolute;left:9px;top:7px}
.nav{left:106px;top:86px;width:496px;height:31px;background:#dedede;border:1px solid #cfcfcf;display:flex;align-items:center;padding-left:4px;font-size:6.5px;color:#444;font-weight:600}
.nav span{padding:0 11px;white-space:nowrap}
.nav .active{background:var(--teal);color:#fff;height:22px;line-height:22px;margin-right:6px}
.card{background:var(--card);box-shadow:0 1px 2px rgba(0,0,0,.12)}
.hero{left:106px;top:126px;width:496px;height:267px}
.hero .photo{left:8px;top:8px;width:480px;height:252px;background:linear-gradient(120deg,#e9d7a5 0%,#6f8a3e 30%,#2d4a1c 70%,#4c6a2b 100%)}
.arrow{top:130px;width:14px;height:17px;background:rgba(255,255,255,.75);font-size:9px;color:#333;text-align:center;line-height:17px}
.sale{left:238px;top:198px;width:150px;height:40px;background:var(--teal-soft);color:#fff;font-family:"Roboto",sans-serif;font-size:12px;display:flex;align-items:center;justify-content:center;gap:4px}
.sale b{font-size:26px;font-weight:400}
.banner{top:409px;width:238px;height:100px}
.banner .photo{left:4px;top:4px;width:230px;height:92px}
.bn1 .photo{background:linear-gradient(90deg,#d4922b,#9c7a36 50%,#4a3416)}
.bn2 .photo{background:linear-gradient(90deg,#566a3a,#7f8e5a 45%,#3a4a2a)}
.bn-title{font-family:"Playfair Display",serif;font-weight:700;color:#fff;line-height:1}
.bn1 .bn-title{left:106px;top:8px;font-size:20px;text-align:center}
.shop{left:124px;top:75px;background:var(--pink);color:#fff;font-size:5.5px;padding:4px 5px;font-family:"Playfair Display",serif}
.bn2 .small{left:106px;top:16px;font-size:6px;font-family:"Playfair Display",serif;color:#fff;line-height:1.2}
.bn2 .bn-title{left:104px;top:34px;font-size:20px}
.bn2 .tags{right:12px;top:64px;font-size:6.5px;font-family:"Playfair Display",serif;color:#fff;line-height:1.05}
.section-bar{left:106px;top:525px;width:496px;height:29px;font-family:"Roboto",sans-serif;font-size:9px;color:#222;font-weight:500;padding:10px 10px}
.sort{right:8px;top:7px;width:53px;height:15px;border:1px solid var(--line);font-size:5.5px;color:#aaa;padding:4px 5px;font-weight:400}
.product{width:116px;height:175px;overflow:hidden}
.product .photo{left:4px;top:4px;width:108px;height:138px}
.price{left:4px;top:119px;width:108px;height:23px;background:var(--teal-soft);color:#fff;font-size:7px;font-weight:600;text-align:center;line-height:23px}
.pname{left:6px;top:148px;width:92px;font-size:7.2px;line-height:9.5px;color:#444}
.ribbon{right:-15px;top:7px;width:56px;height:11px;transform:rotate(45deg);color:#fff;font-size:5px;text-align:center;line-height:11px;font-weight:600}
.divider{left:105px;top:946px;width:498px;height:3px;background:#fff;border-bottom:1px solid var(--line)}
.widget{top:974px;width:158px;height:126px;padding:12px 12px}
.widget h3{font-family:"Roboto",sans-serif;font-weight:400;font-size:9px;color:var(--teal);padding-bottom:6px;border-bottom:1px solid var(--line);margin-bottom:8px}
.widget p{font-size:6px;line-height:11px;color:#777}
.follow{right:15px;top:12px;width:30px;height:10px;background:#e4e8ee;border:1px solid #c5cbd3;border-radius:2px}
.tweet{display:flex;gap:4px;font-size:5.3px;line-height:7px;color:#555;margin-bottom:8px}
.tweet .av{width:14px;height:14px;background:#8a9a7a;flex:none}
.tweet a{color:#3a7bd5;text-decoration:none}
.tweet .d{margin-left:auto;color:#999;white-space:nowrap;flex:none}
.email{width:132px;height:21px;border:1px solid var(--line);font-size:6px;color:#bbb;padding:7px 8px;margin:10px 0 10px}
.submit{width:61px;height:21px;background:var(--teal);color:#fff;font-size:7px;text-align:center;line-height:21px}
.footer{left:0;top:1122px;width:708px;height:78px;background:var(--dark);color:#aaa;font-size:6.5px}
.flinks{left:106px;top:15px;display:flex;gap:6px}
.flinks span+span:before{content:"|";margin-right:6px}
.copy{right:106px;top:15px}
.fline{left:106px;top:34px;width:496px;height:1px;background:#555}
.social{left:106px;top:51px;display:flex;gap:12px}
.social i{width:9px;height:9px;border-radius:50%;background:#eee;display:block}
.pay{right:106px;top:50px;display:flex;gap:3px}
.pay i{width:24px;height:14px;background:#f2f2f2;border-radius:2px;display:block}
</style>
</head>
<body>

<header>
  <div class="abs topbar">
    <div class="abs flag" role="img" aria-label="UK flag"></div>
    <div class="abs cur">USD ⌄</div>
    <div class="abs toplinks"><span>Login</span><span>Register</span><span>My Account</span><span>Wish List (0)</span><span>Checkout</span></div>
  </div>
  <div class="abs brand"><i></i>MirelaStyle</div>
  <div class="abs search">Search...
    <svg width="9" height="9" viewBox="0 0 10 10"><circle cx="4" cy="4" r="3" fill="none" stroke="#bbb" stroke-width="1.2"/><path d="M6.3 6.3 9 9" stroke="#bbb" stroke-width="1.2"/></svg>
  </div>
  <div class="abs cart">0 items - $0.00
    <svg width="13" height="10" viewBox="0 0 13 10"><path d="M0 1h2l2 6h7l1.5-4.5H3" fill="none" stroke="#1b8f9e" stroke-width="1.3"/><circle cx="5" cy="9" r="1" fill="#1b8f9e"/><circle cx="10" cy="9" r="1" fill="#1b8f9e"/></svg>
  </div>
  <nav class="abs nav">
    <span class="active">HOME</span><span>WHAT'S NEW?</span><span>DRESSES</span><span>TOPS</span><span>BOTTOMS/ROMPERS</span><span>ACCESSORIES</span><span>SALE</span><span>A LITTLE ABOUT ME</span>
  </nav>
</header>

<section class="abs card hero">
  <div class="abs photo" role="img" aria-label="Model in patterned summer dress in a sunlit garden"></div>
  <div class="abs arrow" style="left:12px">‹</div>
  <div class="abs arrow" style="right:12px">›</div>
  <div class="abs sale">SALE <b>15%</b> OFFER</div>
</section>

<section class="abs card banner bn1" style="left:106px">
  <div class="abs photo" role="img" aria-label="Model in mustard knit top outdoors"></div>
  <div class="abs bn-title">Holiday<br>Shopping<br>2014</div>
  <div class="abs shop">SHOW NOW</div>
</section>
<section class="abs card banner bn2" style="left:364px">
  <div class="abs photo" role="img" aria-label="Model in orange off-shoulder dress among greenery"></div>
  <div class="abs small">GET<br>EMBELLISHED</div>
  <div class="abs bn-title">ETHNICITY</div>
  <div class="abs tags">MATERNITY<br>DINGOLFI<br>TUMMY</div>
</section>

<div class="abs card section-bar">WHATS NEW!<div class="abs sort">SORT BY ⌄</div></div>

<main>
  <div class="abs card product" style="left:106px;top:569px"><div class="abs photo" style="background:linear-gradient(#f1f1f1,#e2e2e2)" role="img" aria-label="White off-shoulder top"></div><div class="abs price">$.27.00</div><div class="abs ribbon" style="background:var(--red)">NEW</div><div class="abs pname">Lia Bell Sleeve Fringe Tube Top</div></div>
  <div class="abs card product" style="left:233px;top:569px"><div class="abs photo" style="background:linear-gradient(#eeeeee,#d9d5cf)" role="img" aria-label="White crop top with floral shorts"></div><div class="abs price">$.35.00</div><div class="abs pname">Lia Bell Sleeve Fringe Tube Top</div></div>
  <div class="abs card product" style="left:359px;top:569px"><div class="abs photo" style="background:linear-gradient(#6b6a52,#d9d4c8)" role="img" aria-label="White bell sleeve top with black trim"></div><div class="abs price">$.27.00</div><div class="abs ribbon" style="background:var(--magenta)">HOT</div><div class="abs pname">Lia Bell Sleeve Fringe Tube Top</div></div>
  <div class="abs card product" style="left:486px;top:569px"><div class="abs photo" style="background:linear-gradient(90deg,#e7e7ea,#c9a8a8 50%,#e7e7ea)" role="img" aria-label="Patterned flare pants"></div><div class="abs price">$.27.00</div><div class="abs ribbon" style="background:var(--red)">NEW</div><div class="abs pname">Lia Bell Sleeve Fringe Tube Top</div></div>

  <div class="abs card product" style="left:106px;top:756px"><div class="abs photo" style="background:linear-gradient(90deg,#e6e6e6,#2f5a6a 50%,#e6e6e6)" role="img" aria-label="Blue printed flare pants"></div><div class="abs price">$.27.00</div><div class="abs ribbon" style="background:var(--red)">NEW</div><div class="abs pname">Lia Bell Sleeve Fringe Tube Top</div></div>
  <div class="abs card product" style="left:233px;top:756px"><div class="abs photo" style="background:linear-gradient(#ececec,#e8cdd6)" role="img" aria-label="Floral print blouse on hanger"></div><div class="abs price">$.27.00</div><div class="abs pname">Lia Bell Sleeve Fringe Tube Top</div></div>
  <div class="abs card product" style="left:359px;top:756px"><div class="abs photo" style="background:linear-gradient(90deg,#5a5a5a,#eeeeea 50%,#5a5a5a)" role="img" aria-label="White halter tank on dress form"></div><div class="abs price">$.27.00</div><div class="abs ribbon" style="background:var(--blue)">SPECIAL</div><div class="abs pname">Lia Bell Sleeve Fringe Tube Top</div></div>
  <div class="abs card product" style="left:486px;top:756px"><div class="abs photo" style="background:linear-gradient(90deg,#5a5a5a,#a89a62 50%,#5a5a5a)" role="img" aria-label="Olive halter tank on dress form"></div><div class="abs price">$.27.00</div><div class="abs ribbon" style="background:var(--red)">NEW</div><div class="abs pname">Lia Bell Sleeve Fringe Tube Top</div></div>
</main>

<div class="abs divider"></div>

<aside>
  <div class="abs card widget" style="left:106px">
    <h3>A little about me...</h3>
    <p>My name is Rosalie (pronounced Roz-a-lee with a "R") and I have always loved fashion! In 2004, I moved to LA to pursue my love. I have finally made it a reality by opening my own boutique. We currently carry a variety of different labels and hope to incorporate our own in the near future!</p>
  </div>
  <div class="abs card widget" style="left:276px">
    <h3>Latest Tweets</h3>
    <div class="abs follow"></div>
    <div class="tweet"><div class="av"></div><div>MirelaStyle<br>@MirelaStyle<br>New Lena Playsuit added today so amazing for this fall! Shop at <a>mirelastyle.com!</a></div><span class="d">15 Sep</span></div>
    <div class="tweet"><div class="av"></div><div>MirelaStyle<br>@MirelaStyle<br>Awesome new romper added today! Shop at <a>mirelastyle.com</a></div><span class="d">15 Sep</span></div>
  </div>
  <div class="abs card widget" style="left:444px">
    <h3>Newsletter Signup</h3>
    <p>We promise to only send you good things.</p>
    <div class="email">Email Address</div>
    <div class="submit">SUBMIT</div>
  </div>
</aside>

<footer class="abs footer">
  <div class="abs flinks"><span>Search</span><span>About Us</span><span>Products</span><span>Privacy Policy</span><span>Sitemap</span></div>
  <div class="abs copy">Copyrights@ 2014 mirelastyle. All Right Reserved.</div>
  <div class="abs fline"></div>
  <div class="abs social"><i></i><i></i><i></i><i></i><i></i></div>
  <div class="abs pay"><i></i><i></i><i></i><i></i><i></i><i></i><i></i></div>
</footer>

</body>
</html>
```